Building company buisness cards

We are looking for a sharp modern new look for our business cards.
We are a New Zealand based company that specialises in house and land packages.
We have attached a photo of the current logo and would like to see if it can be improved somehow if needed.
We are open to any colours but we have chosen green at this stage.
Feel free to change the font and make the logo smarter looking.
Play with the colours and see what looks best.

We want a card that looks so good know one will want to throw it away!

Target Market(s)

Home buyers

Industry/Entity Type

Building

Contact Information for Business Card

Derek Tolvane
0217394062
dtolvane@quillmarkhomesteads.co.nz
quillmarkhomesteads.co.nz

Font styles to use
Serif
Sans Serif

Colors

Designer to choose colors to be used in the design.

Requirements
Must have
• Logo and company name on one side, details on the other side
Nice to have
• Color codes for the original green are HEX #4a8028, RGB(74,128,40), CMYK(42,0,69,50)
• Round corners, Raised and/or spot UV

```html
<!DOCTYPE html>
<html lang="en">
<head>
<meta charset="utf-8">
<title>Quillmark Homesteads – Business Cards</title>
<link rel="stylesheet" href="https://fonts.googleapis.com/css2?family=Arimo:wght@400&family=Tinos:wght@400&display=swap">
<style>
  :root {
    --backdrop: #3a3a3c;
    --card: #ffffff;
    --brand-green: #1f8f2a;
    --band-green: #249a2c;
    --rule-dark: #3b2320;
    --ink: #222222;
    --ink-soft: #444444;
    --hairline: #d6d6d6;
  }
  * { box-sizing: border-box; margin: 0; padding: 0; }
  html, body {
    width: 1200px;
    height: 716px;
    overflow: hidden;
    background: var(--backdrop);
  }
  .canvas {
    position: relative;
    width: 1200px;
    height: 716px;
  }
  .card {
    position: absolute;
    top: 215px;
    width: 500px;
    height: 286px;
    background: var(--card);
    border-radius: 6px;
    overflow: hidden;
  }
  .card--front { left: 70px; }
  .card--back { left: 630px; }

  .company-name {
    font-family: "Arimo", Arial, sans-serif;
    font-weight: 400;
    color: var(--brand-green);
    text-align: center;
    white-space: nowrap;
  }
  .card--front .company-name {
    position: absolute;
    top: 118px;
    left: 0;
    right: 0;
    font-size: 32px;
    line-height: 40px;
  }
  .front-rule {
    position: absolute;
    top: 196px;
    left: 215px;
    width: 70px;
    height: 1px;
    background: var(--hairline);
  }

  .back-graphic {
    position: absolute;
    inset: 0;
  }
  .details {
    position: absolute;
    top: 70px;
    left: 0;
    right: 0;
    text-align: center;
  }
  .details .company-name {
    font-size: 22px;
    line-height: 28px;
  }
  .contact-name {
    margin-top: 12px;
    font-family: "Arimo", Arial, sans-serif;
    font-size: 17px;
    color: var(--ink);
  }
  .contact-phone {
    margin-top: 4px;
    font-family: "Tinos", "Times New Roman", serif;
    font-size: 13px;
    letter-spacing: 1px;
    color: var(--ink-soft);
  }
  .contact-line {
    margin-top: 3px;
    font-family: "Arimo", Arial, sans-serif;
    font-size: 12px;
    color: var(--ink-soft);
  }
</style>
</head>
<body>
<main class="canvas">
  <section class="card card--front" aria-label="Business card front">
    <h1 class="company-name">Quillmark Homesteads</h1>
    <div class="front-rule"></div>
  </section>

  <section class="card card--back" aria-label="Business card back">
    <svg class="back-graphic" width="500" height="286" viewBox="0 0 500 286" aria-hidden="true">
      <line x1="0" y1="48" x2="500" y2="48" stroke="var(--rule-dark)" stroke-width="2"/>
      <line x1="0" y1="54" x2="500" y2="54" stroke="var(--band-green)" stroke-width="2"/>
      <line x1="0" y1="232" x2="500" y2="232" stroke="var(--band-green)" stroke-width="2"/>
      <line x1="0" y1="238" x2="500" y2="238" stroke="var(--rule-dark)" stroke-width="2"/>
      <rect x="0" y="58" width="500" height="170" fill="var(--band-green)"/>
      <ellipse cx="250" cy="143" rx="165" ry="140" fill="var(--card)"/>
    </svg>
    <div class="details">
      <h2 class="company-name">Quillmark Homesteads</h2>
      <p class="contact-name">Derek Tolvane</p>
      <p class="contact-phone">0217394062</p>
      <p class="contact-line">dtolvane@quillmarkhomesteads.co.nz</p>
      <p class="contact-line">quillmarkhomesteads.co.nz</p>
    </div>
  </section>
</main>
</body>
</html>
```